Cleaning service website design

We need a new nice web design(logo will be the same) for a new cleaning service Company:

Informations about Company and logo you can take from flyers in attachments.

This is a cleaning service Company which have simple rules and we would like to show that(in checklist form) on website:

- What we do and that we're Cleaning Green

- Why us?

- How much(our pricing is simple)

Also we would like to communicate with clients by some nice/big pictures on website and the most important thing is our phone number and short/fast Brimtallow.

Also there should be some space for description about our Company.

Generally all information on main page can be short: about us, about service(what we do), last reviews, tips (for example: Tip of the week) and other can be some introduction to subpage where will be more information.

There will be few subpages like: About us, About our service, Photos(Before and after), Reviews , Tips, FAQ, Contact, Looking for a Job? - most of them will be just text so you can project just one example.

```html
<!DOCTYPE html>
<html lang="en">
<head>
<meta charset="utf-8">
<title>Tidy Nest – House Cleaning</title>
<link href="https://fonts.googleapis.com/css2?family=Open+Sans:wght@400;600;700;800&family=PT+Sans+Narrow&display=swap" rel="stylesheet">
<style>
:root{
  --green:#6fb52c;
  --green-dark:#4f8f1a;
  --blue:#1a5ea8;
  --navy:#0c3f86;
  --ink:#222;
  --text:#333;
  --muted:#999;
  --line:#d4d4d4;
  --panel:#f7f7f7;
  --orange:#f39a0e;
  --orange-dark:#e46c06;
  --red:#d8141b;
  --footer:#262626;
  --footer-bottom:#1c1c1c;
  --white:#fff;
}
*{box-sizing:border-box;margin:0;padding:0}
html,body{width:948px;height:1200px;overflow:hidden;background:var(--white)}
body{position:relative;font-family:"Open Sans",Arial,sans-serif;color:var(--text)}
a{color:inherit;text-decoration:none}
h1,h2,h3{font-weight:inherit}

/* header */
.site-header{position:absolute;left:0;top:0;width:948px;height:100px;border-bottom:4px solid #e8e8e8}
.brand{position:absolute;left:118px;top:22px;display:flex;align-items:center;gap:10px}
.brand-dot{width:44px;height:44px;border-radius:50%;background:var(--green)}
.brand-name{font-size:26px;font-weight:700;color:var(--navy)}
.header-call{position:absolute;right:118px;top:10px;text-align:right;font-size:11px;color:var(--ink)}
.header-call b{font-weight:700}
.header-phone{display:flex;align-items:center;justify-content:flex-end;gap:6px;font-size:19px;font-weight:800;color:var(--ink);margin-top:1px}
.main-nav{position:absolute;left:320px;top:52px;display:flex;height:48px}
.main-nav a{display:block;padding:0 11px;line-height:48px;font-size:9px;font-weight:700;color:var(--ink);text-transform:uppercase}
.main-nav a.active{background:#efefef;color:var(--green);border-bottom:4px solid var(--green);line-height:44px}
.main-nav a+a{margin-left:4px}

/* hero */
.hero{position:absolute;left:0;top:106px;width:948px;height:397px;
  background:radial-gradient(ellipse 120px 200px at 700px 250px,#b3b267 0%,#a3ad4e 40%,transparent 100%),
             radial-gradient(ellipse at 55% 85%,#c9cf6a 0%,transparent 45%),
             linear-gradient(100deg,#4d5e1e 0%,#86a033 35%,#9cb045 55%,#4e5c20 85%,#2c3512 100%)}
.hero-copy{position:absolute;left:118px;top:42px;color:var(--white)}
.hero-title{font-size:29px;font-weight:400;letter-spacing:.5px;line-height:1}
.hero-title strong{font-weight:800}
.hero-sub{font-size:16px;font-weight:700;margin-top:7px;line-height:22px}
.hero-sub .price{font-size:28px;font-weight:800;color:var(--red);vertical-align:-3px}
.checklist{list-style:none;margin-top:6px}
.checklist li{display:flex;align-items:center;gap:9px;height:26.5px;font-size:11.5px;font-weight:600}
.cta{position:absolute;left:118px;top:296px;width:195px;height:46px;border-radius:5px;
  background:linear-gradient(#ffae2a,var(--orange-dark));color:var(--white);
  font-size:19px;font-weight:700;display:flex;align-items:center;justify-content:center;gap:10px}
.hero-badge{position:absolute;left:335px;top:289px;width:56px;height:56px;border-radius:50%;background:#e8f3d6;border:3px solid var(--white)}

/* cards */
.card{position:absolute;top:533px;width:228px;height:270px;border:1px solid var(--line);background:var(--white);box-shadow:0 8px 6px -6px rgba(0,0,0,.25)}
.card-photo{margin:3px;height:86px;background:linear-gradient(90deg,#c9b49a,#e3d4c2,#b8a58c)}
.card-photo.alt{background:linear-gradient(90deg,#d9c6b0,#c4c6c2,#8c9aa6)}
.card-title{text-align:center;color:var(--green);font-size:15px;font-weight:600;margin:9px 0 10px}
.card-clean{left:117px}
.card-pricing{left:359px}
.card-estimate{left:601px}
.task-list{list-style:none;padding:0 10px 0 24px}
.task-list li{position:relative;padding-left:14px;font-size:10px;font-weight:600;color:var(--ink);line-height:15px;margin-bottom:7.5px;letter-spacing:-.1px}
.task-list li::before{content:"";position:absolute;left:0;top:5px;width:5px;height:5px;background:var(--ink)}
.price-list{list-style:none;padding:0 10px 0 28px}
.price-list li{font-size:10px;font-weight:600;color:var(--ink);line-height:15px;margin-bottom:4px;letter-spacing:-.1px}
.price-list .amt{color:var(--green)}
.price-list a{color:var(--blue);text-decoration:underline}
.price-note{padding:0 28px;margin-top:14px;font-size:9px;font-style:italic;font-weight:600;color:var(--ink)}
.estimate-title{text-align:center;color:var(--green);font-size:15px;font-weight:600;margin:12px 0 11px}
.estimate-form{padding:0 24px}
.field{display:block;width:180px;height:23px;border:1px solid #c8c8c8;margin-bottom:10.5px;font-size:8px;line-height:10px;color:var(--muted);padding:6px 9px;white-space:nowrap;overflow:hidden}
.field-row{display:flex;gap:6px}
.field-row .field{width:87px;padding:6px 7px}
.estimate-foot{display:flex;justify-content:space-between;align-items:flex-start;margin-top:8px}
.call-today{font-size:8.5px;font-weight:800;color:var(--ink);line-height:1.1}
.call-today span{display:block;color:var(--blue);font-size:14px;font-weight:700}
.submit{width:66px;height:21px;background:linear-gradient(#f7861c,var(--orange-dark));color:var(--white);font-size:9px;font-weight:700;text-align:center;line-height:21px}

/* about */
.about{position:absolute;left:117px;top:837px;width:712px;height:113px;border:1px solid var(--line);background:var(--panel)}
.about-photo{position:absolute;left:3px;bottom:0;width:176px;height:126px;background:linear-gradient(90deg,#2b2f36,#4a4e55,#c9b18a);border-radius:60px 60px 0 0}
.about-title{position:absolute;left:185px;top:18px;font-family:"PT Sans Narrow",Arial,sans-serif;font-size:22px;font-weight:400;color:var(--ink)}
.about-text{position:absolute;left:185px;top:50px;width:508px;font-size:9.3px;line-height:14.8px;color:var(--text)}
.read-more{position:absolute;right:18px;bottom:10px;color:var(--green);font-size:8px;font-weight:700}

/* footer */
.site-footer{position:absolute;left:0;top:982px;width:948px;height:186px;background:var(--footer);color:var(--white)}
.footer-col{position:absolute;top:32px}
.footer-col h3{font-size:12px;font-weight:700;margin-bottom:9px}
.footer-col ul{list-style:none}
.footer-col li{font-size:9px;font-weight:600;line-height:18.5px;padding-left:1px}
.newsletter p{font-size:9px;font-weight:600;margin-bottom:8px}
.signup{display:flex;gap:6px}
.signup-input{width:241px;height:32px;background:var(--white);border-radius:3px;color:var(--ink);font-size:9px;font-weight:600;padding:10px 11px}
.signup-go{width:32px;height:32px;border-radius:3px;background:linear-gradient(#ffb22e,var(--orange-dark));color:var(--white);font-size:10px;font-weight:700;text-align:center;line-height:32px}
.social{display:flex;gap:8px;margin-top:27px}
.social span{width:18px;height:18px;border-radius:2px}
.social .s1{background:#1f5fb0}.social .s2{background:#2ea6de}.social .s3{background:#f08a1c}
.footer-brand{position:absolute;right:118px;top:126px;display:flex;align-items:center;gap:6px}
.footer-brand .brand-dot{width:24px;height:24px}
.footer-brand .brand-name{font-size:15px;color:var(--white)}
.footer-bottom{position:absolute;left:0;top:1168px;width:948px;height:32px;background:var(--footer-bottom);color:#5e5e5e;font-size:8px;padding:10px 118px}
</style>
</head>
<body>

<header class="site-header">
  <a class="brand" href="#"><span class="brand-dot"></span><span class="brand-name">Tidy Nest</span></a>
  <div class="header-call">
    <div><b>Call Us</b> to arrange your cleaning on</div>
    <div class="header-phone">
      <svg width="13" height="16" viewBox="0 0 13 16" aria-hidden="true"><path d="M3 1 L6 4 L4.5 6 Q6 10 9 12 L11 10.5 L13 13.5 L10.5 15.5 Q2 13 1 3 Z" fill="#1a5ea8"/></svg>
      <span>555-014-2290</span>
    </div>
  </div>
  <nav class="main-nav">
    <a class="active" href="#">Home</a><a href="#">About Us</a><a href="#">Our Services</a><a href="#">Photos</a><a href="#">Reviews</a><a href="#">Tips</a><a href="#">Careers</a><a href="#">FAQ</a><a href="#">Contact</a>
  </nav>
</header>

<section class="hero" role="img" aria-label="Woman with outstretched arms in a sunny green forest path">
  <div class="hero-copy">
    <h1 class="hero-title">SIMPLIFY <strong>YOUR LIFE</strong></h1>
    <p class="hero-sub">and some there House Cleaning from <span class="price">$79</span></p>
    <ul class="checklist">
      <li><svg width="18" height="20" viewBox="0 0 18 20" aria-hidden="true"><path d="M2 19 Q1 6 17 1 Q16 15 2 19 Z" fill="#5fae22"/></svg>Locally Owned &amp; Operated</li>
      <li><svg width="18" height="20" viewBox="0 0 18 20" aria-hidden="true"><path d="M2 19 Q1 6 17 1 Q16 15 2 19 Z" fill="#5fae22"/></svg>Reliable &amp; Affordable</li>
      <li><svg width="18" height="20" viewBox="0 0 18 20" aria-hidden="true"><path d="M2 19 Q1 6 17 1 Q16 15 2 19 Z" fill="#5fae22"/></svg>All Supplies Provided</li>
      <li><svg width="18" height="20" viewBox="0 0 18 20" aria-hidden="true"><path d="M2 19 Q1 6 17 1 Q16 15 2 19 Z" fill="#5fae22"/></svg>No Contracts</li>
      <li><svg width="18" height="20" viewBox="0 0 18 20" aria-hidden="true"><path d="M2 19 Q1 6 17 1 Q16 15 2 19 Z" fill="#5fae22"/></svg>Pet Friendly</li>
      <li><svg width="18" height="20" viewBox="0 0 18 20" aria-hidden="true"><path d="M2 19 Q1 6 17 1 Q16 15 2 19 Z" fill="#5fae22"/></svg>Green Cleaning</li>
    </ul>
  </div>
  <a class="cta" href="#">GET STARTED
    <svg width="22" height="18" viewBox="0 0 22 18" aria-hidden="true"><path d="M0 6 H12 V0 L22 9 L12 18 V12 H0 Z" fill="#fff"/></svg>
  </a>
  <span class="hero-badge" aria-hidden="true"></span>
</section>

<article class="card card-clean">
  <div class="card-photo" role="img" aria-label="Family with a dog relaxing on a sofa"></div>
  <h2 class="card-title">What do we clean?</h2>
  <ul class="task-list">
    <li>Thoroughly clean your bathrooms, kitchen, bedrooms and living areas</li>
    <li>Mop or vacuum your floors</li>
    <li>Dust surfaces</li>
    <li>Collect garbage</li>
    <li>Make beds</li>
  </ul>
</article>

<article class="card card-pricing">
  <div class="card-photo alt" role="img" aria-label="Parents and daughter looking at a laptop together"></div>
  <h2 class="card-title">Pricing is..simple</h2>
  <ul class="price-list">
    <li><span class="amt">$79</span> for homes less than 1000 sq ft</li>
    <li><span class="amt">$89</span> for homes 1000-1800 sq ft</li>
    <li><span class="amt">$99</span> for homes 1800-2600 sq ft</li>
    <li>If your home is larger than 2600 sq ft please <a href="#">call for a quote</a></li>
  </ul>
  <p class="price-note">*rates are for regular service*</p>
</article>

<aside class="card card-estimate">
  <h2 class="estimate-title">Quick Brimtallow</h2>
  <div class="estimate-form">
    <span class="field">Name</span>
    <span class="field">E-mail</span>
    <span class="field">Postal Code</span>
    <span class="field">Phone</span>
    <div class="field-row"><span class="field">No. of Bathrooms</span><span class="field">No. of Bedrooms</span></div>
    <div class="estimate-foot">
      <div class="call-today">CALL US TODAY<span>555-014-2290</span></div>
      <span class="submit">SUBMIT</span>
    </div>
  </div>
</aside>

<section class="about">
  <div class="about-photo" role="img" aria-label="Portrait of the two company owners"></div>
  <h2 class="about-title">About Tidy Nest</h2>
  <p class="about-text">It's about caring, not just cleaning. Having personally experienced the struggles of finding quality maid service for our home, we want to make it simpler for families in the Brookvale area. Our goal is to provide caring, consistent and reliable house cleaning to every customer we serve.</p>
  <a class="read-more" href="#">READ MORE...</a>
</section>

<footer class="site-footer">
  <div class="footer-col" style="left:118px">
    <h3>Quick Links</h3>
    <ul><li>Home</li><li>About Us</li><li>Our Service</li><li>Photos</li><li>Contact</li></ul>
  </div>
  <div class="footer-col" style="left:261px">
    <h3>Useful Links</h3>
    <ul><li>Terms of use</li><li>Privacy Policy</li><li>Help Center</li><li>Community</li><li>Login Area</li></ul>
  </div>
  <div class="footer-col" style="left:388px">
    <h3>Join Our Community</h3>
    <ul><li>Chatterbook</li><li>Peeplet</li><li>Workring</li></ul>
  </div>
  <div class="footer-col newsletter" style="left:549px">
    <h3>SignUp For Our Monthly Newsletter</h3>
    <p>Subscribe our newsletter &amp; get the latest news &amp; updates</p>
    <div class="signup"><span class="signup-input">Email Address</span><span class="signup-go">GO</span></div>
    <div class="social" aria-label="Social links"><span class="s1"></span><span class="s2"></span><span class="s3"></span></div>
  </div>
  <div class="footer-brand"><span class="brand-dot"></span><span class="brand-name">Tidy Nest</span></div>
</footer>
<div class="footer-bottom">© 2013 by, Tidy Nest. All Rights Reserved.</div>

</body>
</html>
```